My project benefits Military, First Responders, Police, Fire, and Educators.

Contact Information for Business Card

2 Sided appointment card. Visual side will have my head shot with "Brisk Lantern" in a bold graffic/text. I am picturing maybe the headshot applied to a filter that has a matrix effect where the picture is made up of data/numbers flowing vertically through the photo. I am of course open to other concepts as well. Side two will have contact info presented in an attractive visual complimenting the front.

```html
<!DOCTYPE html>
<html lang="en">
<head>
<meta charset="utf-8">
<title>Brisk Lantern – Appointment Card</title>
<link rel="stylesheet" href="https://fonts.googleapis.com/css2?family=Source+Sans+3:wght@400;600;700&display=swap">
<style>
  :root {
    --backdrop: #3a3230;
    --card-dark: #111214;
    --card-light: #f7f7f5;
    --brand-blue: #1f5fb0;
    --brand-teal: #2fb89a;
    --text-white: #f2f2f2;
    --text-blue: #2a5aa8;
    --photo-top: #2b2b2e;
    --photo-mid: #b07a5e;
    --photo-suit: #14203a;
  }
  * { margin: 0; padding: 0; box-sizing: border-box; }
  html, body { width: 1200px; height: 844px; overflow: hidden; }
  body {
    background: var(--backdrop);
    font-family: "Source Sans 3", sans-serif;
    position: relative;
  }
  .card {
    position: absolute;
    top: 262px;
    width: 540px;
    height: 320px;
    border-radius: 4px;
    overflow: hidden;
    box-shadow: 0 12px 30px rgba(0,0,0,0.45);
  }
  .card--front { left: 40px; background: var(--card-dark); }
  .card--back  { left: 620px; background: var(--card-light); }

  .brand-name {
    font-weight: 700;
    color: var(--brand-blue);
    line-height: 1;
    display: flex;
    align-items: center;
    gap: 10px;
    white-space: nowrap;
  }
  .brand-dot {
    width: 12px; height: 12px; border-radius: 50%;
    background: var(--brand-teal);
    flex: none;
  }
  .card--front .brand-name {
    position: absolute; left: 34px; top: 70px;
    font-size: 30px;
    max-width: 240px;
  }
  .card--back .brand-name { position: absolute; right: 34px; top: 34px; font-size: 30px; }

  .headshot {
    position: absolute;
    right: 0; top: 0;
    width: 250px; height: 320px;
    background: linear-gradient(180deg, var(--photo-top) 0%, var(--photo-mid) 38%, var(--photo-mid) 50%, var(--photo-suit) 72%, var(--photo-suit) 100%);
  }

  .person { position: absolute; left: 34px; top: 150px; }
  .person-name { color: var(--text-blue); font-weight: 600; font-size: 21px; line-height: 1.1; }
  .person-role { color: var(--text-white); font-size: 16px; }

  .contact-list { position: absolute; left: 34px; top: 212px; list-style: none; }
  .contact-list li {
    color: var(--text-white);
    font-size: 17px;
    line-height: 25px;
    display: flex; align-items: center; gap: 10px;
  }
  .contact-list svg { width: 12px; height: 12px; fill: var(--text-blue); flex: none; }

  .appointment { position: absolute; left: 40px; top: 130px; right: 40px; }
  .appointment-title { color: var(--brand-teal); font-size: 19px; font-weight: 600; margin-bottom: 14px; }
  .appointment-field {
    display: flex; align-items: baseline; gap: 6px;
    color: var(--text-blue); font-size: 15px;
    margin-bottom: 26px;
  }
  .appointment-line { flex: 1; border-bottom: 2px dotted var(--text-blue); }
  .appointment-note { color: var(--brand-teal); font-size: 15px; font-weight: 600; }
</style>
</head>
<body>
  <section class="card card--front">
    <div class="brand-name"><span class="brand-dot"></span>Brisk Lantern</div>
    <div class="headshot" role="img" aria-label="Head-and-shoulders portrait of the managing director in a dark suit and tie"></div>
    <div class="person">
      <p class="person-name">Daniel Brooks</p>
      <p class="person-role">Managing Director</p>
    </div>
    <ul class="contact-list">
      <li><svg viewBox="0 0 12 12"><path d="M2.5 0.5 L4.5 0.5 L5 3.5 L3.6 4.5 Q5 7.2 7.5 8.4 L8.5 7 L11.5 7.5 L11.5 9.5 Q11 11.5 9 11.5 Q0.5 10.5 0.5 3 Q0.5 1 2.5 0.5 Z"/></svg>044-987 654 321</li>
      <li><svg viewBox="0 0 12 12"><path d="M0 2 H12 V10 H0 Z M0.8 2.6 L6 6.6 L11.2 2.6 V2.8 L6 7.4 L0.8 2.8 Z" fill-rule="evenodd"/></svg>hello@brisklantern.com</li>
      <li><svg viewBox="0 0 12 12"><circle cx="6" cy="6" r="5.5"/></svg>www.brisklantern.com</li>
    </ul>
  </section>

  <section class="card card--back">
    <div class="brand-name"><span class="brand-dot"></span>Brisk Lantern</div>
    <div class="appointment">
      <p class="appointment-title">Appointment</p>
      <div class="appointment-field"><span>Name :</span><span class="appointment-line"></span></div>
      <div class="appointment-field"><span>Date :</span><span class="appointment-line"></span></div>
      <p class="appointment-note">If unable to keep appointment, kindly give 24hrs notice.</p>
    </div>
  </section>
</body>
</html>
```